Kelvara Pane Works Business Card

We need a business card design that is suitable for a Glazing Business. We Specialize in Repairing broken windows and doors and are a 24hr on call service. We manufacture Shower screens, Fly screens, Wardrobe doors, Security doors and grilles + mirrors. We stock a variety of mesh including Standard mesh, Pet resistant mesh, Tressmet & Clearweft. We would like to use a combination of Light Blue, Dark Blue, Black & White with perhaps a picture of glass breaking.

Industry/Entity Type

Business

Contact Information for Business Card

Narooma Glass Service60B Glasshouse Rocks RdNarooma NSW 2546PH / FAX - 02 44765210MOB - 0419682350 Andrewemail - kelvarapane@fenmail.example

Font styles to use
Serif

Colors
34a7d8
0255a3
ffffff

Requirements
Must have
• logo with picture of broken or cracked glass

```html
<!DOCTYPE html>
<html lang="en">
<head>
<meta charset="utf-8">
<title>Kelvara Pane Works – Business Card</title>
<link rel="stylesheet" href="https://fonts.googleapis.com/css2?family=Source+Sans+3:wght@400;600&display=swap">
<style>
  :root {
    --page-bg: #2b2724;
    --card-black: #0c0c0d;
    --light-blue: #34a7d8;
    --dark-blue: #0255a3;
    --white: #ffffff;
    --silver: #c9cbcd;
    --text-soft: #e6e8ea;
  }
  * { box-sizing: border-box; margin: 0; padding: 0; }
  html, body {
    width: 1200px; height: 900px; overflow: hidden;
    background: var(--page-bg);
    font-family: "Source Sans 3", Arial, sans-serif;
  }
  .stage {
    position: relative; width: 1200px; height: 900px;
    display: flex; align-items: center; justify-content: center; gap: 40px;
  }
  .card {
    position: relative; width: 540px; height: 310px;
    background: var(--card-black);
    box-shadow: 0 10px 30px rgba(0,0,0,.5);
    color: var(--text-soft);
  }

  /* Front: contact side */
  .brand {
    position: absolute; left: 40px; top: 128px; width: 250px;
    font-weight: 600; font-size: 26px; line-height: 1.1;
    color: var(--light-blue); letter-spacing: .5px;
    display: flex; align-items: center; gap: 10px;
  }
  .brand-dot {
    flex: none; width: 16px; height: 16px; border-radius: 50%;
    background: var(--light-blue);
  }
  .divider {
    position: absolute; left: 305px; top: 40px; width: 1px; height: 230px;
    background: linear-gradient(to bottom, transparent, var(--light-blue) 20%, var(--dark-blue) 80%, transparent);
  }
  .contact {
    position: absolute; left: 325px; top: 44px; right: 16px;
    font-size: 14px; line-height: 1.4;
  }
  .contact-name {
    font-weight: 600; font-size: 19px; color: var(--light-blue); margin-bottom: 2px;
  }
  .contact-address { margin-bottom: 22px; }
  .contact-list { list-style: none; }
  .contact-list li { display: flex; align-items: center; gap: 9px; height: 22px; }
  .contact-list svg { width: 12px; height: 12px; flex: none; fill: var(--light-blue); }
  .contact-email { font-size: 13px; }

  /* Back: services side */
  .card--back .brand {
    position: absolute; left: 0; right: 0; top: 92px; width: auto;
    justify-content: center; font-size: 36px; color: var(--silver);
  }
  .card--back .brand-dot { width: 22px; height: 22px; background: var(--silver); }
  .services {
    position: absolute; left: 0; right: 0; top: 176px;
    text-align: center; font-size: 15px; line-height: 1.5; color: var(--text-soft);
  }
  .service { white-space: nowrap; margin: 0 3px; }
  .service::before {
    content: ""; display: inline-block; width: 9px; height: 9px; border-radius: 50%;
    background: var(--light-blue); margin-right: 4px; vertical-align: 0;
  }
</style>
</head>
<body>
<main class="stage">
  <section class="card card--front" aria-label="Business card front">
    <div class="brand"><span class="brand-dot"></span><span>Kelvara Pane Works</span></div>
    <div class="divider"></div>
    <div class="contact">
      <p class="contact-name">Malcolm</p>
      <p class="contact-address">17C Tindale Ridge Rd<br>Brenmoor NSW 2583</p>
      <ul class="contact-list">
        <li><svg viewBox="0 0 12 12" aria-hidden="true"><path d="M2.5 0.8 4.3 3 3.4 4.3c.7 1.6 2 2.9 3.6 3.6L8.3 7l2.2 1.8-1 2C5 10.6 1.4 7 1.2 2.5z"/></svg>02 48931067</li>
        <li><svg viewBox="0 0 12 12" aria-hidden="true"><path d="M3 1h5v3H3zM1 5h10v6H1zm2 2v1h2V7zm0 2v1h2V9zm4-2v1h2V7z"/></svg>02 48931067</li>
        <li><svg viewBox="0 0 12 12" aria-hidden="true"><path d="M3 0h6v12H3zm1 1.5v7.5h4V1.5zM5.4 10h1.2v1H5.4z"/></svg>0419682350</li>
        <li class="contact-email"><svg viewBox="0 0 12 12" aria-hidden="true"><path d="M0 2h12v1L6 7 0 3zm0 2.3 6 4 6-4V10H0z"/></svg>kelvarapane@fenmail.example</li>
      </ul>
    </div>
  </section>

  <section class="card card--back" aria-label="Business card back">
    <div class="brand"><span class="brand-dot"></span><span>Kelvara Pane Works</span></div>
    <p class="services">
      <span class="service">Shower screens</span><span class="service">Fly screens</span><span class="service">Wardrobe doors</span><br>
      <span class="service">Security doors</span><span class="service">Grilles + mirrors</span>
    </p>
  </section>
</main>
</body>
</html>
```